Business Cards for IT Consulting Company (Managed Service Provider)

I am looking to have some business cards printed and would like some designs. We are an IT Consulting company based in Vancouver BC. I would like a nice clean and modern look to the cards. I have uploaded all the versions of my logo so parts can be used as needed. Here is a snippit from our website homepage:

Quillbrook Networks Ltd. is an IT Solutions Partner located in Vancouver BC, Canada. We offer IT solutions and support to customers in the greater Vancouver Area. With expertise in Microsoft platforms, as well as Linux and Mac OSX and over 12 years experience in the IT industry, Quillbrook Networks is dedicated to offering our clients top quality service and products. We take pride in the solutions we offer our customers. The greatest compliment a client can give us is to recommend our services.

Quillbrook Networks Ltd. offers a wide range of IT services from onsite service to remote support and managed service solutions. This allows clients to choose the support path that best suits their company’s needs. Supporting many different sized companies from small to enterprise level over the past 12 years Quillbrook Networks has the experience and expertise needed to ensure things run smoothly. Allowing our clients to focus on doing business.

Revolutionizing the way IT services are delivered.

Quillbrook Networks is dedicated to providing our clients with IT solutions that work and grow with them for years to come. This philosophy helps save money in the long run instead of replacing equipment constantly. Far too often IT solutions are not well thought out and while possibly solving the problem at hand, require replacement due to growth or quality within a very short time frame. Quillbrook Networks takes pride in providing solutions that will last and be able to accommodate growth without the need for replacement.

Industry/Entity Type

Information Technology

Contact Information for Business Card

Quillbrook Networks Ltd.
(Employee Name)
Eml: (Employees Email Address)
Web: quillbrook.me
Ph: 604-555-0148

Font styles to use
Serif
Sans Serif

Requirements
Must have
• The Company logo and company colors.
Nice to have
• - Our tag line: "Revolutionizing IT Services" or "Revolutionizing the way IT services are delivered."
• - Also I really like the idea of nature and technology together blending which is sort of where my logo came from so integrating that somehow onto the business cards would be great.

```html
<!DOCTYPE html>
<html lang="en">
<head>
<meta charset="utf-8">
<title>Quillbrook Networks Ltd. — Business Cards</title>
<link href="https://fonts.googleapis.com/css2?family=Montserrat:wght@600&family=Roboto:ital,wght@0,400;0,500;1,400&display=swap" rel="stylesheet">
<style>
  :root {
    --backdrop: #a9a7a8;
    --card: #f4f4f4;
    --brand-blue: #1e8fd6;
    --brand-grey: #4b4a4c;
    --text-grey: #555558;
  }
  * { margin: 0; padding: 0; box-sizing: border-box; }
  html, body { width: 1200px; height: 1200px; overflow: hidden; }
  body { background: var(--backdrop); position: relative; font-family: "Roboto", Arial, sans-serif; }

  .card { position: absolute; width: 712px; height: 417px; background: var(--card); overflow: hidden; }
  .card--front { left: 238px; top: 120px; }
  .card--back { left: 231px; top: 645px; }

  .brand { position: absolute; display: flex; align-items: center; gap: 26px; }
  .brand__mark { width: 58px; height: 58px; background: var(--brand-blue); flex: none; }
  .brand__name { font-family: "Montserrat", Arial, sans-serif; font-weight: 600; color: var(--brand-blue); line-height: 1; }
  .brand__name .line1 { display: block; font-size: 62px; letter-spacing: -0.5px; }
  .brand__name .line2 { display: block; font-size: 24px; letter-spacing: 1px; margin-top: 6px; }

  .card--front .brand { left: 112px; top: 140px; }
  .card--back .brand { left: 50px; top: 52px; }
  .card--back .brand__mark { width: 48px; height: 48px; }
  .card--back .brand__name .line1 { font-size: 56px; }
  .card--back .brand__name .line2 { font-size: 22px; }

  .tagline { position: absolute; left: 0; right: 0; top: 374px; display: flex; justify-content: center; align-items: center; gap: 16px; color: var(--text-grey); font-size: 18px; letter-spacing: 0.3px; }
  .tagline::before, .tagline::after { content: ""; width: 108px; height: 3px; background: var(--brand-blue); }

  .contact { position: absolute; left: 416px; top: 196px; color: var(--text-grey); }
  .contact__name { font-size: 25px; font-weight: 500; color: var(--brand-blue); letter-spacing: 0.3px; }
  .contact__title { font-size: 16px; font-style: italic; margin-top: 6px; }
  .contact__list { list-style: none; margin-top: 26px; }
  .contact__list li { display: flex; align-items: center; gap: 14px; font-size: 18px; height: 27.5px; }
  .contact__list svg { width: 16px; height: 16px; flex: none; fill: var(--brand-blue); }

  .band { position: absolute; left: 0; bottom: 0; width: 712px; height: 20px; }
</style>
</head>
<body>
  <section class="card card--front">
    <div class="brand">
      <span class="brand__mark"></span>
      <span class="brand__name"><span class="line1">Quillbrook</span><span class="line2">NETWORKS LTD.</span></span>
    </div>
    <p class="tagline">Revolutionizing IT Services</p>
  </section>

  <section class="card card--back">
    <div class="brand">
      <span class="brand__mark"></span>
      <span class="brand__name"><span class="line1">Quillbrook</span><span class="line2">NETWORKS LTD.</span></span>
    </div>
    <div class="contact">
      <p class="contact__name">Daniel Hart</p>
      <p class="contact__title">Managing Director</p>
      <ul class="contact__list">
        <li><svg viewBox="0 0 16 16" aria-hidden="true"><path d="M1 6c0-2 3-4 7-4s7 2 7 4v1h-4V5.5H5V7H1z"/><rect x="3" y="8" width="10" height="6" rx="1"/></svg>604-555-0148</li>
        <li><svg viewBox="0 0 16 16" aria-hidden="true"><circle cx="8" cy="8" r="7" fill="none" stroke="#1e8fd6" stroke-width="1.5"/><ellipse cx="8" cy="8" rx="3" ry="7" fill="none" stroke="#1e8fd6" stroke-width="1.2"/><path d="M1 8h14" stroke="#1e8fd6" stroke-width="1.2"/></svg>www.quillbrook.me</li>
        <li><svg viewBox="0 0 16 16" aria-hidden="true"><rect x="1" y="3" width="14" height="10"/><path d="M1 3l7 6 7-6" fill="none" stroke="#f4f4f4" stroke-width="1.3"/></svg>support@quillbrook.me</li>
      </ul>
    </div>
    <svg class="band" viewBox="0 0 712 20" aria-hidden="true">
      <polygon points="0,2 500,2 480,20 0,20" fill="#1e8fd6"/>
      <polygon points="506,2 712,2 712,20 486,20" fill="#4b4a4c"/>
    </svg>
  </section>
</body>
</html>
```